Velvet Circle club

We are looking to redesign the user interface of our mobile app “Velvet Circle”, which is the official rewards program for our luxury casino brand, Kestrane Harbour.
Our goal is to give the app a more elegant, premium, and user-friendly design that reflects the exclusivity of our brand and the luxury experience we offer our VIP clientele.
What We Need:
A complete UI design for the app’s main screens, including:
Splash Screen
01 Login / Signup Screen
02 Home Dashboard
Buttons -
Home / my card / my wallet / my booking / my host
My wallet / my offer / lucky game / my taxi / entertainment / online
03 Profile screen
04 My wallet
05 My offer
06Packages
07 My booking
08 My host
09 My card
we attached our privies app all the screen for you reference
Inspiration:
Think of luxury brands like Dunmore-Vale, Corvix Onyx, or high-end lifestyle apps. Clean interfaces, classy animations, and a sense of exclusivity are key.
We’re excited to see fresh, innovative takes that elevate the app to a truly world-class luxury experience for our users.
Thank you!
Casino

```html
<!DOCTYPE html>
<html lang="en">
<head>
<meta charset="utf-8">
<title>Velvet Circle — App Screens</title>
<link href="https://fonts.googleapis.com/css2?family=Mulish:wght@400;500;600;700;800&display=swap" rel="stylesheet">
<style>
:root{
  --stage:#b8aea8;
  --screen:#ffffff;
  --band:#ebe8e4;
  --ink:#1f1a18;
  --muted:#4a4442;
  --soft:#6d6866;
  --brown:#563a2c;
  --brown-grey:#5e4f4e;
  --gold:#f0a020;
  --line:#e6e3e0;
  --shadow:0 1px 4px rgba(0,0,0,.14);
}
*{box-sizing:border-box;margin:0;padding:0}
html,body{width:1200px;height:689px;overflow:hidden}
body{background:var(--stage);font-family:'Mulish',sans-serif;color:var(--ink);position:relative}
.phone{position:absolute;top:60px;width:287px;height:555px;background:var(--screen);border-radius:28px;overflow:hidden}
.phone--login{left:92px}
.phone--home{left:465px}
.phone--info{left:838px}

/* login */
.login-head{position:absolute;left:0;top:0;width:100%;height:144px;background:var(--band)}
.status{position:absolute;left:14px;top:6px;right:14px;display:flex;justify-content:space-between;align-items:center;font-size:12px;font-weight:500}
.status svg{margin-left:4px}
.brand{position:absolute;left:0;right:0;top:46px;text-align:center;color:var(--gold)}
.brand-mark{width:26px;height:26px;border-radius:50%;background:var(--gold);margin:0 auto 6px}
.brand-name{font-size:21px;font-weight:800;letter-spacing:.5px;line-height:1}
.brand-sub{font-size:9px;font-weight:700;margin-top:4px;letter-spacing:1px}
.card{position:absolute;left:14px;width:260px;height:123px;background:#fff;box-shadow:var(--shadow);border-radius:3px;text-align:center;padding-top:14px}
.card--member{top:162px}
.card--new{top:300px}
.card h2{font-size:14px;font-weight:600;margin-bottom:5px}
.card p{font-size:10.2px;line-height:18px;color:var(--muted);padding:0 14px}
.btn{display:inline-flex;align-items:center;justify-content:center;gap:5px;color:#fff;font-weight:700;border-radius:20px}
.card .btn{width:97px;height:31px;font-size:13px;margin-top:5px}
.btn--dark{background:var(--brown)}
.btn--grey{background:var(--brown-grey)}
.or{position:absolute;top:434px;left:0;right:0;text-align:center;font-size:12px;font-weight:700}
.temp-note{position:absolute;top:458px;left:0;right:0;text-align:center;font-size:10.2px;color:var(--muted)}
.btn--temp{position:absolute;left:67px;top:506px;width:155px;height:35px;font-size:13px}

/* home */
.topbar{position:absolute;left:0;top:0;width:100%;height:43px;background:var(--band)}
.topbar .menu{position:absolute;left:15px;top:14px}
.topbar .bell{position:absolute;right:14px;top:13px}
.banner{position:absolute;left:0;top:43px;width:100%;height:165px;background:linear-gradient(135deg,#1e2a7a 0%,#3a3d9a 40%,#b89a3a 70%,#233080 100%)}
.menu-list{position:absolute;left:14px;top:222px;width:259px;list-style:none}
.menu-item{height:35px;background:#fff;box-shadow:var(--shadow);border-radius:3px;margin-bottom:9px;display:flex;align-items:center;padding:0 12px;font-size:12px;color:var(--ink)}
.menu-item svg.ic{margin-right:9px}
.menu-item .go{margin-left:auto}

/* info */
.info-head{position:absolute;left:0;top:0;width:100%;height:48px;background:var(--band);display:flex;align-items:center;justify-content:center;font-size:14px;font-weight:600}
.info-head .back{position:absolute;left:14px;top:18px}
.info-head .bell{position:absolute;right:14px;top:17px}
.info-body{position:absolute;left:15px;top:60px;width:260px;font-size:8.6px;line-height:16px;color:var(--soft)}
.info-body p{margin-bottom:16px}
.info-body ul{list-style:none}
.info-body li{padding-left:7px;position:relative}
.info-body li::before{content:"•";position:absolute;left:0}

/* nav */
.tabbar{position:absolute;left:0;bottom:0;width:100%;height:63px;border-top:1px solid var(--line);background:#fff}
.tab{position:absolute;top:16px;transform:translateX(-50%);display:flex;flex-direction:column;align-items:center;font-size:7.6px;color:var(--muted);white-space:nowrap}
.tab svg{margin-bottom:3px}
.tab--active{font-size:9px;font-weight:700;color:var(--ink);top:14px}
</style>
</head>
<body>

<!-- Login screen -->
<section class="phone phone--login">
  <div class="login-head">
    <div class="status">
      <span>9:41</span>
      <span>
        <svg width="12" height="9" viewBox="0 0 12 9"><path d="M1 3a7 7 0 0 1 10 0M3 5a4 4 0 0 1 6 0" stroke="#000" stroke-width="1.4" fill="none"/><circle cx="6" cy="7.5" r="1.1"/></svg>
        <svg width="11" height="9" viewBox="0 0 11 9"><rect x="0" y="7" width="2" height="2"/><rect x="3" y="5" width="2" height="4"/><rect x="6" y="3" width="2" height="6"/><rect x="9" y="0" width="2" height="9"/></svg>
        <svg width="15" height="9" viewBox="0 0 15 9"><rect x=".5" y=".5" width="12" height="8" rx="1.5" fill="none" stroke="#000"/><rect x="2" y="2" width="8" height="5"/><rect x="13" y="3" width="1.5" height="3"/></svg>
      </span>
    </div>
    <div class="brand">
      <div class="brand-mark"></div>
      <div class="brand-name">VELVET CIRCLE</div>
      <div class="brand-sub">CLUB</div>
    </div>
  </div>

  <div class="card card--member">
    <h2>Member Login</h2>
    <p>Now you can enjoy all the excitement of the casino right at your fingertips.</p>
    <span class="btn btn--dark">Sign In
      <svg width="12" height="11" viewBox="0 0 12 11"><path d="M5 1H2v9h3" stroke="#fff" stroke-width="1.6" fill="none"/><path d="M4 4h4V1.5L11.5 5.5 8 9.5V7H4z" fill="#fff"/></svg>
    </span>
  </div>

  <div class="card card--new">
    <h2>New Member Login</h2>
    <p>If you are a first time user, please go through the sign up process</p>
    <span class="btn btn--grey">Sign Up
      <svg width="12" height="13" viewBox="0 0 12 13"><rect x="1" y="1" width="8" height="11" rx="1" fill="#fff"/><path d="M3 4h4M3 6h4M3 8h2" stroke="#5e4f4e" stroke-width="1"/><path d="M7 10l4-5" stroke="#fff" stroke-width="1.6"/></svg>
    </span>
  </div>

  <div class="or">OR</div>
  <div class="temp-note">If you are with a temporary ID, sign in here</div>
  <span class="btn btn--dark btn--temp">Temporary Sign In</span>
</section>

<!-- Home screen -->
<section class="phone phone--home">
  <div class="topbar">
    <svg class="menu" width="15" height="12" viewBox="0 0 15 12"><path d="M1 1h13M1 6h10M1 11h13" stroke="#222" stroke-width="1.6" stroke-linecap="round"/></svg>
    <svg class="bell" width="12" height="13" viewBox="0 0 12 13"><path d="M6 1a4 4 0 0 1 4 4v3l1.5 2h-11L2 8V5a4 4 0 0 1 4-4z" fill="#111"/><circle cx="6" cy="11.5" r="1.3" fill="#111"/></svg>
  </div>
  <div class="banner" role="img" aria-label="Festive Eid event promotion banner with featured performers"></div>

  <ul class="menu-list">
    <li class="menu-item"><svg class="ic" width="15" height="13" viewBox="0 0 15 13"><rect x="1" y="3" width="12" height="9" rx="1" fill="#555"/><path d="M3 3l7-2 1 2" stroke="#555" fill="none"/><rect x="9" y="6" width="5" height="3" fill="#fff" stroke="#555"/></svg>My Wallet<svg class="go" width="10" height="9" viewBox="0 0 10 9"><path d="M1 4.5h8M5.5 1l3.5 3.5L5.5 8" stroke="#333" stroke-width="1.3" fill="none"/></svg></li>
    <li class="menu-item"><svg class="ic" width="15" height="15" viewBox="0 0 15 15"><circle cx="7.5" cy="7.5" r="6.5" fill="#555"/><path d="M5 10l5-5" stroke="#fff" stroke-width="1.2"/><circle cx="5.2" cy="5.2" r="1" fill="#fff"/><circle cx="9.8" cy="9.8" r="1" fill="#fff"/></svg>My Offer<svg class="go" width="10" height="9" viewBox="0 0 10 9"><path d="M1 4.5h8M5.5 1l3.5 3.5L5.5 8" stroke="#333" stroke-width="1.3" fill="none"/></svg></li>
    <li class="menu-item"><svg class="ic" width="15" height="15" viewBox="0 0 15 15"><circle cx="7.5" cy="7.5" r="6.5" fill="none" stroke="#555" stroke-width="1.4"/><circle cx="7.5" cy="7.5" r="4" fill="#555"/><path d="M6 5.5h3L7 10" stroke="#fff" stroke-width="1.1" fill="none"/></svg>Lucky Game<svg class="go" width="10" height="9" viewBox="0 0 10 9"><path d="M1 4.5h8M5.5 1l3.5 3.5L5.5 8" stroke="#333" stroke-width="1.3" fill="none"/></svg></li>
    <li class="menu-item"><svg class="ic" width="16" height="13" viewBox="0 0 16 13"><path d="M3 5l2-4h6l2 4h1.5v5h-13V5z" fill="#555"/><rect x="2" y="10" width="3" height="2.5" fill="#555"/><rect x="11" y="10" width="3" height="2.5" fill="#555"/><circle cx="4.5" cy="7.5" r="1" fill="#fff"/><circle cx="11.5" cy="7.5" r="1" fill="#fff"/></svg>My Taxi<svg class="go" width="10" height="9" viewBox="0 0 10 9"><path d="M1 4.5h8M5.5 1l3.5 3.5L5.5 8" stroke="#333" stroke-width="1.3" fill="none"/></svg></li>
    <li class="menu-item"><svg class="ic" width="15" height="15" viewBox="0 0 15 15"><circle cx="7.5" cy="7.5" r="6.5" fill="#555"/><circle cx="7.5" cy="3.8" r="1.6" fill="#fff"/><circle cx="7.5" cy="11.2" r="1.6" fill="#fff"/><circle cx="3.8" cy="7.5" r="1.6" fill="#fff"/><circle cx="11.2" cy="7.5" r="1.6" fill="#fff"/></svg>Entertainment<svg class="go" width="10" height="9" viewBox="0 0 10 9"><path d="M1 4.5h8M5.5 1l3.5 3.5L5.5 8" stroke="#333" stroke-width="1.3" fill="none"/></svg></li>
    <li class="menu-item"><svg class="ic" width="16" height="14" viewBox="0 0 16 14"><rect x="1" y="2" width="14" height="10" rx="1" fill="none" stroke="#555" stroke-width="1.4"/><rect x="3" y="5" width="5" height="5" fill="#555"/><path d="M10 5h3M10 7h3" stroke="#555"/><path d="M0 13h16" stroke="#555" stroke-width="1.4"/></svg>Online<svg class="go" width="10" height="9" viewBox="0 0 10 9"><path d="M1 4.5h8M5.5 1l3.5 3.5L5.5 8" stroke="#333" stroke-width="1.3" fill="none"/></svg></li>
  </ul>

  <nav class="tabbar">
    <div class="tab" style="left:25px"><svg width="14" height="13" viewBox="0 0 14 13"><path d="M1.5 6L7 1.5 12.5 6v6H9V8.5H5V12H1.5z" fill="none" stroke="#333" stroke-width="1.3"/></svg>Home</div>
    <div class="tab" style="left:71px"><svg width="12" height="13" viewBox="0 0 12 13"><circle cx="6" cy="4" r="3" fill="none" stroke="#333" stroke-width="1.3"/><path d="M1 12.5v-2a3 3 0 0 1 3-3h4a3 3 0 0 1 3 3v2z" fill="none" stroke="#333" stroke-width="1.3"/></svg>My Card</div>
    <div class="tab tab--active" style="left:132px"><svg width="16" height="14" viewBox="0 0 16 14"><rect x="1" y="3" width="13" height="10" rx="1" fill="#333"/><path d="M3 3l7-2.5 1.5 2.5" stroke="#333" fill="none"/><rect x="10" y="6.5" width="5" height="3.5" fill="#fff" stroke="#333"/></svg>My Wallet</div>
    <div class="tab" style="left:200px"><svg width="14" height="14" viewBox="0 0 14 14"><rect x="1" y="2.5" width="12" height="10.5" rx="1" fill="none" stroke="#333" stroke-width="1.3"/><path d="M1 5.5h12M4 1v3M10 1v3M4.5 9l2 1.8L10 7.5" stroke="#333" stroke-width="1.2" fill="none"/></svg>My Booking</div>
    <div class="tab" style="left:257px"><svg width="13" height="15" viewBox="0 0 13 15"><rect x="1" y="1" width="11" height="13" rx="1" fill="none" stroke="#333" stroke-width="1.3"/><circle cx="6.5" cy="6" r="2" fill="none" stroke="#333"/><path d="M3.5 11.5a3 3 0 0 1 6 0" stroke="#333" fill="none"/></svg>My Host</div>
  </nav>
</section>

<!-- Responsible gaming screen -->
<section class="phone phone--info">
  <header class="info-head">
    <svg class="back" width="7" height="11" viewBox="0 0 7 11"><path d="M6 1L1.5 5.5 6 10" stroke="#222" stroke-width="1.6" fill="none"/></svg>
    Responsible Gaming
    <svg class="bell" width="12" height="13" viewBox="0 0 12 13"><path d="M6 1a4 4 0 0 1 4 4v3l1.5 2h-11L2 8V5a4 4 0 0 1 4-4z" fill="#111"/><circle cx="6" cy="11.5" r="1.3" fill="#111"/></svg>
  </header>
  <div class="info-body">
    <p>Kestrane Harbour fully understands the importance of responsible gaming and promotes a sensible,careful behaviouramongst its clients. Our commitments is to a gaming that maintains a healthy atm... We want to see each of our customers to take pleasure in a responsible gaming experience in a friendly and comfortable enviroment.Responsible gaming means that the harmful potential of gambling is minimized and the the players are in the condition of the making sensible,rational choice-with the help...</p>
    <p style="margin-bottom:0">Kestrane Harbour's guidelines for responsible gaming are thought out with the pleasant stay of everyone at the casino in mind.A respon...</p>
    <ul>
      <li>Is always in control of his/her action.</li>
      <li>Has fun and friendly, doesn't view this as a profession or a contest.</li>
      <li>Remembers that gambling is a type of entertainment, not a lifelong commitment.</li>
      <li>Gambles us ng money that aren't core to his lifestyle i.e. Household income.</li>
      <li>Absolutely never relies on borrowing money to gamble.</li>
      <li>Has a clear limits on his/her spendings and knows when to stop.</li>
      <li>Takes occasional pauses to refresh his mind, body and maod.</li>
      <li>Doesn't intrude in what other clients are playing and how they are doing it.</li>
    </ul>
  </div>

  <nav class="tabbar">
    <div class="tab" style="left:25px"><svg width="14" height="13" viewBox="0 0 14 13"><path d="M1.5 6L7 1.5 12.5 6v6H9V8.5H5V12H1.5z" fill="none" stroke="#333" stroke-width="1.3"/></svg>Home</div>
    <div class="tab" style="left:71px"><svg width="12" height="13" viewBox="0 0 12 13"><circle cx="6" cy="4" r="3" fill="none" stroke="#333" stroke-width="1.3"/><path d="M1 12.5v-2a3 3 0 0 1 3-3h4a3 3 0 0 1 3 3v2z" fill="none" stroke="#333" stroke-width="1.3"/></svg>My Card</div>
    <div class="tab tab--active" style="left:132px"><svg width="16" height="14" viewBox="0 0 16 14"><rect x="1" y="3" width="13" height="10" rx="1" fill="#333"/><path d="M3 3l7-2.5 1.5 2.5" stroke="#333" fill="none"/><rect x="10" y="6.5" width="5" height="3.5" fill="#fff" stroke="#333"/></svg>My Wallet</div>
    <div class="tab" style="left:200px"><svg width="14" height="14" viewBox="0 0 14 14"><rect x="1" y="2.5" width="12" height="10.5" rx="1" fill="none" stroke="#333" stroke-width="1.3"/><path d="M1 5.5h12M4 1v3M10 1v3M4.5 9l2 1.8L10 7.5" stroke="#333" stroke-width="1.2" fill="none"/></svg>My Booking</div>
    <div class="tab" style="left:257px"><svg width="13" height="15" viewBox="0 0 13 15"><rect x="1" y="1" width="11" height="13" rx="1" fill="none" stroke="#333" stroke-width="1.3"/><circle cx="6.5" cy="6" r="2" fill="none" stroke="#333"/><path d="M3.5 11.5a3 3 0 0 1 6 0" stroke="#333" fill="none"/></svg>My Host</div>
  </nav>
</section>

</body>
</html>
```